Suds Haven Laundromat Wordpress Design

We need a Wordpress website design for our laundromat, Suds Haven Atlanta, at www.sudshavenatlanta-example.com. We would like to have 6 pages: Home, About Us, Services, Locations, Reviews and Contact us. We will provide content for the text on each page. What we do: We are a full service laundromat that provides dry cleaning drop off, professional laundry services, wash dry fold and self service laundry to the local community. We would like to use the color scheme from our logo to convey a warm, safe, and bright business that caters to its diverse community.
Updates

I like the structure of this laundromat website: http://www.washtroveusa-example.com/ Using my logo and color scheme in the above referenced website is what. Am looking for. The photos attached to the project with the female model should be used as a primary focus and supplemented by actual photos of the equipment.

Target Market(s)

Our target market is a diverse group of people from Midtown Atlanta - LGBTQ community /Locals/Regulars that have been coming to laundromat for 30 years.

Industry/Entity Type

Laundromat

Coding

Coded - Design and coding required

Number of Pages Required

5+ page

Font styles to use
Sans Serif

Colors
0054AA
0677BA
7BADD7
CADEEF
E8F1F8

Requirements
Must have
• Feature this video on the main page: https://videohost-example.com/xq7Rm2bPz4k

```html
<!DOCTYPE html>
<html lang="en">
<head>
<meta charset="utf-8">
<title>Suds Haven – A Full Service Laundromat</title>
<link href="https://fonts.googleapis.com/css2?family=Montserrat:wght@500;600;700&family=Arimo:ital,wght@0,400;0,700;1,400&display=swap" rel="stylesheet">
<style>
:root{
  --blue:#1f8fd6;
  --blue-deep:#0677ba;
  --navy:#1c4f97;
  --navy-dark:#184888;
  --ink:#333;
  --muted:#555;
  --pale:#e8f1f8;
  --star:#f0a21a;
  --white:#fff;
}
*{margin:0;padding:0;box-sizing:border-box}
html,body{width:1200px;height:3920px;overflow:hidden;background:var(--white)}
body{position:relative;font-family:'Arimo',Arial,sans-serif;color:var(--ink)}
.abs{position:absolute}
.head-font{font-family:'Montserrat',Arial,sans-serif}

/* header */
.site-header{position:absolute;left:0;top:0;width:1200px;height:142px;background:var(--white)}
.brand{position:absolute;left:110px;top:28px;display:flex;align-items:center;gap:12px}
.brand-dot{width:22px;height:22px;border-radius:50%;background:var(--blue)}
.brand-name{font-family:'Montserrat',sans-serif;font-weight:700;font-size:30px;color:var(--navy);line-height:1}
.brand-tag{position:absolute;left:144px;top:78px;font-size:12px;color:var(--blue);letter-spacing:.3px}
.main-nav{position:absolute;top:64px;left:421px;display:flex;font-family:'Montserrat',sans-serif;font-weight:600;font-size:14px;color:#222}
.main-nav a{text-decoration:none;color:inherit;position:absolute;white-space:nowrap}
.main-nav a.active{color:var(--blue)}

/* hero */
.hero{position:absolute;left:0;top:142px;width:1200px;height:770px;overflow:hidden}
.hero-photo{position:absolute;inset:0;background:linear-gradient(180deg,#9fb8b9 0%,#7f8c8a 35%,#6b6b66 60%,#8d8b86 100%)}
.hero-wave{position:absolute;left:0;bottom:0;width:1200px;height:160px}
.hero-banner{position:absolute;left:111px;background:rgba(31,143,214,.9);color:var(--white);font-family:'Montserrat',sans-serif;font-weight:500;font-size:29px;letter-spacing:1px;padding:0 29px;height:65px;line-height:65px}

/* section titles */
.section-title{position:absolute;left:0;width:1200px;text-align:center;font-family:'Montserrat',sans-serif;font-weight:600;font-size:36px;color:var(--navy)}
.section-title span{color:var(--blue)}
.title-rule{position:absolute;left:580px;width:40px;height:3px;background:var(--blue)}

/* service cards */
.service-card{position:absolute;top:1039px;width:310px;height:498px;background:var(--white);box-shadow:0 2px 6px rgba(0,0,0,.15);border-bottom:4px solid var(--blue);text-align:center}
.service-photo{height:246px;background:linear-gradient(160deg,#c9cfcc,#8c9391 60%,#b7bcba)}
.service-icon{position:absolute;left:110px;top:200px;width:90px;height:90px;border-radius:50%;background:var(--white);display:flex;align-items:center;justify-content:center}
.service-name{margin-top:50px;font-family:'Montserrat',sans-serif;font-weight:600;font-size:17px;color:#222;letter-spacing:.5px}
.service-text{margin:20px auto 0;width:260px;font-size:13px;line-height:26px;color:var(--muted)}
.btn-outline{display:inline-block;margin-top:16px;width:130px;height:48px;line-height:44px;border:2px solid var(--blue);border-radius:24px;font-family:'Montserrat',sans-serif;font-weight:600;font-size:14px;color:var(--blue)}

/* welcome */
.welcome-wave{position:absolute;left:0;top:1620px;width:1200px;height:720px}
.welcome-photo{position:absolute;left:136px;top:1768px;width:408px;height:408px;border-radius:50%;background:radial-gradient(circle at 40% 40%,#b8764a,#6e8aa0 55%,#2f5fa8);border:6px solid var(--navy)}
.welcome-kicker{position:absolute;left:608px;top:1832px;font-family:'Montserrat',sans-serif;font-weight:500;font-size:25px;color:var(--white)}
.welcome-title{position:absolute;left:608px;top:1872px;font-family:'Montserrat',sans-serif;font-weight:600;font-size:35px;color:var(--white);letter-spacing:.5px}
.welcome-text{position:absolute;left:608px;top:1935px;width:466px;font-size:13.3px;line-height:25.8px;color:var(--white);text-align:justify}
.btn-light{position:absolute;left:609px;top:2145px;width:166px;height:56px;line-height:52px;border:2px solid var(--white);border-radius:28px;text-align:center;font-family:'Montserrat',sans-serif;font-weight:600;font-size:15px;color:var(--white)}

/* testimonials */
.quote-card{position:absolute;top:2487px;width:315px;height:291px;background:var(--white);box-shadow:0 1px 6px rgba(0,0,0,.18);padding:40px 20px 0 20px}
.quote-top{display:flex;align-items:center;gap:12px}
.quote-mark{font-family:Georgia,serif;font-weight:700;font-size:40px;color:#888;line-height:20px;height:20px}
.stars{color:var(--star);font-size:16px;letter-spacing:2px}
.quote-text{margin-top:18px;font-style:italic;font-size:13px;line-height:23.2px;color:var(--muted)}
.reviewer{position:absolute;top:2793px;display:flex;align-items:center;gap:16px}
.reviewer-photo{width:64px;height:64px;border-radius:50%;background:linear-gradient(135deg,#c9a58a,#6d5a4e)}
.reviewer-name{font-family:'Montserrat',sans-serif;font-weight:600;font-size:17px;color:var(--blue)}
.reviewer-role{font-style:italic;font-size:14px;color:var(--muted);margin-top:4px}

/* what we do */
.wwd-photo{position:absolute;left:0;top:2953px;width:710px;height:550px;background:linear-gradient(180deg,#bcc5c0 0%,#8f9893 50%,#5d6360 100%)}
.wwd-panel{position:absolute;left:642px;top:3062px;width:558px;height:441px;background:var(--white)}
.wwd-title{position:absolute;left:688px;top:3036px;font-family:'Montserrat',sans-serif;font-weight:600;font-size:36px;color:var(--blue)}
.wwd-rule{position:absolute;left:689px;top:3094px;width:52px;height:3px;background:var(--blue)}
.wwd-text{position:absolute;left:688px;top:3118px;width:400px;font-size:13.5px;line-height:25.5px;color:var(--muted);text-align:justify}
.wwd-list{position:absolute;left:688px;top:3220px;list-style:none;font-size:13.5px;color:var(--ink)}
.wwd-list li{height:31.8px;display:flex;align-items:center;gap:30px}
.wwd-list svg{flex:none}

/* footer */
.site-footer{position:absolute;left:0;top:3502px;width:1200px;height:418px;background:var(--navy)}
.foot-title{position:absolute;font-family:'Montserrat',sans-serif;font-weight:600;font-size:24px;color:var(--white);letter-spacing:.5px}
.field{position:absolute;background:var(--white);font-size:11px;color:#333;padding:10px 12px}
.btn-submit{position:absolute;left:111px;top:3773px;width:99px;height:36px;line-height:36px;background:var(--blue);color:var(--white);text-align:center;font-family:'Montserrat',sans-serif;font-weight:600;font-size:14px}
.contact-icon{position:absolute;width:40px;height:40px;border-radius:50%;border:2px solid var(--white);display:flex;align-items:center;justify-content:center}
.contact-text{position:absolute;color:var(--white);font-size:13px;line-height:21px}
.contact-label{font-family:'Montserrat',sans-serif;font-weight:500;font-size:17px}
.foot-brand{position:absolute;left:806px;top:3618px;display:flex;align-items:center;gap:12px}
.foot-brand .brand-name{color:var(--white)}
.foot-brand .brand-dot{background:var(--white)}
.foot-tag{position:absolute;left:886px;top:3660px;font-size:12px;color:var(--white)}
.social{position:absolute;top:3709px;width:34px;height:34px;border-radius:50%;border:2px solid var(--white)}
.copyright{position:absolute;left:0;top:3872px;width:1200px;text-align:center;font-size:15px;color:var(--white)}
</style>
</head>
<body>

<header class="site-header">
  <div class="brand"><span class="brand-dot"></span><span class="brand-name">Suds Haven</span></div>
  <div class="brand-tag">A FULL SERVICE LAUNDROMAT</div>
  <nav class="main-nav">
    <a class="active" style="left:0">HOME</a>
    <a style="left:90px">ABOUT US</a>
    <a style="left:212px">SERVICES</a>
    <a style="left:328px">LOCATIONS</a>
    <a style="left:458px">REVIEWS</a>
    <a style="left:570px">CONTACT US</a>
  </nav>
</header>

<section class="hero">
  <div class="hero-photo" role="img" aria-label="Woman in a blue dress walking between rows of front-loading washers in the laundromat"></div>
  <div class="hero-banner" style="top:401px">SUDS HAVEN</div>
  <div class="hero-banner" style="top:477px">A FULL SERVICES LAUNDROMAT</div>
  <svg class="hero-wave" viewBox="0 0 1200 160" preserveAspectRatio="none">
    <path d="M0,130 C200,140 380,60 620,30 C860,0 1000,50 1200,70 L1200,160 L0,160 Z" fill="var(--blue)"/>
    <path d="M0,150 C200,160 380,80 620,48 C860,18 1000,68 1200,90 L1200,160 L0,160 Z" fill="var(--white)"/>
  </svg>
</section>

<h2 class="section-title" style="top:940px">OUR <span>SERVICES</span></h2>
<div class="title-rule" style="top:997px"></div>

<article class="service-card" style="left:111px">
  <div class="service-photo" role="img" aria-label="Row of top-loading washers"></div>
  <div class="service-icon"><svg width="46" height="46" viewBox="0 0 46 46" fill="none" stroke="var(--blue)" stroke-width="2"><path d="M4 8 Q23 16 42 8"/><path d="M14 12 L8 20 L13 22 L13 40 L33 40 L33 22 L38 20 L32 12 Q23 18 14 12Z"/></svg></div>
  <h3 class="service-name">DRY CLEAN SERVICES</h3>
  <p class="service-text">Sed ut perspiciatis unde omnis iste natus error sit voluptatem accusantium dolorem laudantium, totam rem aperiam</p>
  <span class="btn-outline">READ MORE</span>
</article>
<article class="service-card" style="left:445px">
  <div class="service-photo" role="img" aria-label="Aisle of stacked washers and dryers"></div>
  <div class="service-icon"><svg width="46" height="46" viewBox="0 0 46 46" fill="none" stroke="var(--blue)" stroke-width="2"><path d="M16 6 L30 6 L40 14 L40 40 L6 40 L6 14 Z"/><path d="M23 6 L23 40"/><path d="M16 6 L23 14 L30 6"/></svg></div>
  <h3 class="service-name">LEATHER &amp; SUEDE</h3>
  <p class="service-text">Sed ut perspiciatis unde omnis iste natus error sit voluptatem accusantium dolorem laudantium, totam rem aperiam</p>
  <span class="btn-outline">READ MORE</span>
</article>
<article class="service-card" style="left:779px">
  <div class="service-photo" role="img" aria-label="Large front-loading washing machines"></div>
  <div class="service-icon"><svg width="46" height="46" viewBox="0 0 46 46" fill="none" stroke="var(--blue)" stroke-width="2"><rect x="8" y="4" width="30" height="38" rx="3"/><path d="M8 12 H38"/><circle cx="23" cy="27" r="9"/><circle cx="23" cy="27" r="5"/></svg></div>
  <h3 class="service-name">WASH,DRY,FOLD</h3>
  <p class="service-text">Sed ut perspiciatis unde omnis iste natus error sit voluptatem accusantium dolorem laudantium, totam rem aperiam</p>
  <span class="btn-outline">READ MORE</span>
</article>

<svg class="welcome-wave" viewBox="0 0 1200 720" preserveAspectRatio="none">
  <path d="M0,50 C200,-20 420,20 640,80 C860,140 1060,80 1200,70 L1200,680 C1000,760 760,700 520,640 C300,590 120,620 0,620 Z" fill="var(--blue)"/>
</svg>
<div class="welcome-photo" role="img" aria-label="Portrait of a red-haired woman in a blue dress beside a washer"></div>
<div class="welcome-kicker">WELCOME TO</div>
<div class="welcome-title">SUDS HAVEN</div>
<p class="welcome-text">Sed ut perspiciatis unde omnis iste natus error sit voluptatem accusantium doloremque laudantium, totam rem aperiam, eaque ipsa quae ab illo in ven tore veritatis et quasi architecto beatae vitae dicta sunt explicabo. Nemo enim ipsam voluptatem quia voluptas sit aspernatur aut odit aut fugit, sed quia consequuntur magni dolores eos qui ratione voluptatem sequi nesciunt. Neque porro quisquam est, qui dolorem ipsum quia dolor sit amet, ut labore et dolore magnam aliquam quaerat voluptatem.</p>
<span class="btn-light">LEARN MORE</span>

<h2 class="section-title" style="top:2391px">OUR <span>TESTIMONIALS</span></h2>
<div class="title-rule" style="top:2448px"></div>

<article class="quote-card" style="left:111px"><div class="quote-top"><span class="quote-mark">&ldquo;</span><span class="stars">★★★★★</span></div><p class="quote-text">Sed ut perspiciatis unde omnis iste natus err or sit voluptatem accusantium dolorem que laudantium, totam rem aperiam, eaq ue ipsa quae ab illo inventore veritatis et quasi arch ecto beatae vitae dicta sunt explicabo.Nemo enim ipsam voluptatem quia voluptas sit as pernatur aut odit aut fugit......</p></article>
<article class="quote-card" style="left:443px"><div class="quote-top"><span class="quote-mark">&ldquo;</span><span class="stars">★★★★★</span></div><p class="quote-text">Sed ut perspiciatis unde omnis iste natus err or sit voluptatem accusantium dolorem que laudantium, totam rem aperiam, eaq ue ipsa quae ab illo inventore veritatis et quasi arch ecto beatae vitae dicta sunt explicabo.Nemo enim ipsam voluptatem quia voluptas sit as pernatur aut odit aut fugit......</p></article>
<article class="quote-card" style="left:774px"><div class="quote-top"><span class="quote-mark">&ldquo;</span><span class="stars">★★★★★</span></div><p class="quote-text">Sed ut perspiciatis unde omnis iste natus err or sit voluptatem accusantium dolorem que laudantium, totam rem aperiam, eaq ue ipsa quae ab illo inventore veritatis et quasi arch ecto beatae vitae dicta sunt explicabo.Nemo enim ipsam voluptatem quia voluptas sit as pernatur aut odit aut fugit......</p></article>

<div class="reviewer" style="left:111px"><div class="reviewer-photo" role="img" aria-label="Reviewer portrait"></div><div><div class="reviewer-name">Jhon Smith</div><div class="reviewer-role">Sed ut perspiciatis unde</div></div></div>
<div class="reviewer" style="left:443px"><div class="reviewer-photo" role="img" aria-label="Reviewer portrait"></div><div><div class="reviewer-name">Jhon Smith</div><div class="reviewer-role">Sed ut perspiciatis unde</div></div></div>
<div class="reviewer" style="left:774px"><div class="reviewer-photo" role="img" aria-label="Reviewer portrait"></div><div><div class="reviewer-name">Jhon Smith</div><div class="reviewer-role">Sed ut perspiciatis unde</div></div></div>

<div class="wwd-photo" role="img" aria-label="Woman in a blue dress pushing a laundry cart past front-loading dryers"></div>
<div class="wwd-panel"></div>
<h2 class="wwd-title">WHAT WE DO</h2>
<div class="wwd-rule"></div>
<p class="wwd-text">Sed ut perspiciatis unde omnis iste natus error sit voluptatem accusantium doloremque laudantium, totam rem aperiam, beatae vitae dicta sunt explicabo.</p>
<ul class="wwd-list">
  <li><svg width="14" height="12" viewBox="0 0 14 12"><path d="M1 6 L5 10 L13 1" fill="none" stroke="var(--blue)" stroke-width="2.5"/></svg>In Business over 45 years</li>
  <li><svg width="14" height="12" viewBox="0 0 14 12"><path d="M1 6 L5 10 L13 1" fill="none" stroke="var(--blue)" stroke-width="2.5"/></svg>Voted "BEST COIN LAUNDRY" - Multiple years</li>
  <li><svg width="14" height="12" viewBox="0 0 14 12"><path d="M1 6 L5 10 L13 1" fill="none" stroke="var(--blue)" stroke-width="2.5"/></svg>One of Atlanta's First, Finest, &amp; Friendliest Coin Laundries</li>
  <li><svg width="14" height="12" viewBox="0 0 14 12"><path d="M1 6 L5 10 L13 1" fill="none" stroke="var(--blue)" stroke-width="2.5"/></svg>The best Wash-Dry-Fold in town</li>
  <li><svg width="14" height="12" viewBox="0 0 14 12"><path d="M1 6 L5 10 L13 1" fill="none" stroke="var(--blue)" stroke-width="2.5"/></svg>Cool - Comfortable - Clean</li>
  <li><svg width="14" height="12" viewBox="0 0 14 12"><path d="M1 6 L5 10 L13 1" fill="none" stroke="var(--blue)" stroke-width="2.5"/></svg>Over 50 well maintained machines</li>
  <li><svg width="14" height="12" viewBox="0 0 14 12"><path d="M1 6 L5 10 L13 1" fill="none" stroke="var(--blue)" stroke-width="2.5"/></svg>Commercial Accounts</li>
</ul>

<footer class="site-footer"></footer>
<div class="foot-title" style="left:114px;top:3562px">CONATCT US</div>
<div class="field" style="left:114px;top:3621px;width:180px;height:35px">First Name :</div>
<div class="field" style="left:304px;top:3621px;width:181px;height:35px">Last Name :</div>
<div class="field" style="left:114px;top:3665px;width:180px;height:35px">Email :</div>
<div class="field" style="left:304px;top:3665px;width:181px;height:35px">Phone :</div>
<div class="field" style="left:114px;top:3710px;width:371px;height:55px">Message :</div>
<div class="btn-submit">SUBMIT</div>

<div class="foot-title" style="left:549px;top:3562px">ADDRESS</div>
<div class="contact-icon" style="left:543px;top:3619px"><svg width="14" height="18" viewBox="0 0 14 18"><path d="M7 1 C3 1 1 4 1 7 C1 11 7 17 7 17 C7 17 13 11 13 7 C13 4 11 1 7 1Z" fill="none" stroke="#fff" stroke-width="2"/><circle cx="7" cy="7" r="2" fill="#fff"/></svg></div>
<div class="contact-text" style="left:598px;top:3620px">2210 Magnolia Row NE<br>#118, Atlanta, GA 30399,<br>United States</div>
<div class="contact-icon" style="left:543px;top:3686px"><svg width="16" height="16" viewBox="0 0 16 16"><path d="M3 1 L6 4 L4.5 6 C5.5 8 8 10.5 10 11.5 L12 10 L15 13 L13 15 C7 15 1 9 1 3Z" fill="#fff"/></svg></div>
<div class="contact-text" style="left:600px;top:3694px"><div class="contact-label">PHONE</div>(404) 555-0142</div>
<div class="contact-icon" style="left:543px;top:3753px"><svg width="16" height="12" viewBox="0 0 16 12"><rect x="0" y="0" width="16" height="12" rx="1" fill="#fff"/><path d="M0 1 L8 7 L16 1" fill="none" stroke="var(--navy)" stroke-width="1.5"/></svg></div>
<div class="contact-text" style="left:600px;top:3760px"><div class="contact-label">EMAIL</div>hello@sudshaven-example.com</div>

<div class="foot-brand"><span class="brand-dot"></span><span class="brand-name">Suds Haven</span></div>
<div class="foot-tag">A FULL SERVICE LAUNDROMAT</div>
<span class="social" style="left:838px"></span>
<span class="social" style="left:880px"></span>
<span class="social" style="left:922px"></span>
<span class="social" style="left:964px"></span>
<span class="social" style="left:1010px"></span>

<div class="copyright">© Copyright 2021 Suds Haven.All Rights Reserved</div>

</body>
</html>
```